Contemporary new French wine brand needs logo and series of label design

to design a new contemporary logo and series of labels for a new French wine brand. We hope to attract not just current French wine drinkers but new ones who may appreciate a less traditional and more modern style.
Updates

Reason: we are wanting to extend the project for a few days more to receive more submissions since we had fewer designs submitted than we were expecting, maybe because of the holidays.

Target Market(s)

people who follow the arts community (eg. music, theatre, visual/video arts, dance) --- all mature ages.

Industry/Entity Type

French Wine

Requirements
Must have
• a clear, memorable treatment for the name MORIVAL with accompanying logo.
Nice to have
• embossing, matte/gloss refinement, tasteful foil stamping, coated stock for the whites to help the integrity of the paper in and out of ice buckets. A combo of say, three types of fonts; a semi custom font for the brand name Morival and maybe a script and one other.
Should not have
• not traditional French

```html
<!DOCTYPE html>
<html lang="en">
<head>
<meta charset="utf-8">
<title>Morival – Cabernet Franc Label Series</title>
<link href="https://fonts.googleapis.com/css2?family=Cinzel:wght@500&family=Libre+Caslon+Text:wght@400&family=Great+Vibes&display=swap" rel="stylesheet">
<style>
  :root {
    --page: #ffffff;
    --gold: #e9c46a;
    --gold-deep: #c9a05a;
    --gold-line: #f0b133;
    --tile-light: #e6cf8e;
    --tile-dark: #b8944c;
    --ink: #1c1a19;
    --red-light: #c72a45;
    --red-dark: #5e0d17;
    --black-light: #46413f;
    --black-dark: #0b0909;
    --fine-print-red: #e3a3ad;
    --fine-print-black: #a39a96;
    --script: #d4c2b2;
  }
  * { box-sizing: border-box; margin: 0; padding: 0; }
  html, body { width: 783px; height: 1200px; overflow: hidden; background: var(--page); }
  .canvas { position: relative; width: 783px; height: 1200px; }

  .brand-tile {
    position: absolute; left: 311px; top: 47px; width: 152px; height: 178px;
    display: flex; flex-direction: column;
  }
  .brand-tile .scene {
    flex: 1; background: linear-gradient(180deg, #c9a869, var(--tile-dark) 60%, #a98a45);
    display: flex; align-items: flex-start; justify-content: center; padding-top: 28px;
  }
  .brand-tile .name {
    font-family: "Cinzel", serif; font-weight: 500; font-size: 20px; color: var(--ink); letter-spacing: 2px;
  }
  .brand-tile .rule { height: 8px; background: linear-gradient(90deg, #e6a51f, #f6dc8e, #e6a51f); }

  .label {
    position: absolute; top: 580px; width: 212px; height: 262px;
    display: flex; flex-direction: column; align-items: center;
    border-bottom: 4px solid var(--gold-line);
  }
  .label--red { left: 102px; background: linear-gradient(90deg, var(--red-dark), var(--red-light) 45%, var(--red-dark) 85%, #3a060c); }
  .label--black { left: 460px; background: linear-gradient(90deg, #141212, var(--black-light) 45%, #171414 80%, var(--black-dark)); }

  .label .crest {
    width: 56px; height: 64px;
    background: linear-gradient(160deg, var(--tile-light), #d8b872 60%, #b99049);
    border-bottom: 2px solid var(--gold-line);
    display: flex; align-items: flex-start; justify-content: center; padding-top: 10px;
  }
  .label .crest span { font-family: "Cinzel", serif; font-size: 8px; color: var(--ink); letter-spacing: 0.5px; }

  .label .wordmark {
    margin-top: 38px; font-family: "Cinzel", serif; font-weight: 500; font-size: 27px;
    color: var(--gold); letter-spacing: 2px; line-height: 1;
  }

  .label .varietal {
    margin-top: 50px; font-family: "Libre Caslon Text", serif; font-weight: 400; font-size: 10px; color: var(--gold-deep);
    letter-spacing: 0.3px; padding-bottom: 2px; border-bottom: 1px solid var(--gold-deep);
  }
  .label .vintage { margin-top: 3px; font-family: "Libre Caslon Text", serif; font-weight: 400; font-size: 10px; color: var(--gold); }

  .label .footer {
    position: absolute; left: 12px; right: 12px; bottom: 14px;
    display: flex; justify-content: space-between; align-items: baseline;
  }
  .label .origin { font-family: "Great Vibes", cursive; font-size: 12px; color: var(--script); }
  .label .fine { font-family: "Libre Caslon Text", serif; font-size: 7px; width: 40px; letter-spacing: 0.2px; }
  .label--red .fine { color: var(--fine-print-red); }
  .label--black .fine { color: var(--fine-print-black); }
  .label .fine.right { text-align: right; }
</style>
</head>
<body>
<main class="canvas">

  <section class="brand-tile">
    <div class="scene" role="img" aria-label="Engraved vineyard landscape with farmhouse, rising sun and rows of vines in gold tones">
      <span class="name">MORIVAL</span>
    </div>
    <div class="rule"></div>
  </section>

  <article class="label label--red">
    <div class="crest" role="img" aria-label="Small gold vineyard engraving tile"><span>MORIVAL</span></div>
    <h1 class="wordmark">MORIVAL</h1>
    <p class="varietal">CABERNET FRANK</p>
    <p class="vintage">2015</p>
    <div class="footer">
      <span class="fine">750 ML</span>
      <span class="origin">Product of France</span>
      <span class="fine right">12% ALC</span>
    </div>
  </article>

  <article class="label label--black">
    <div class="crest" role="img" aria-label="Small gold vineyard engraving tile"><span>MORIVAL</span></div>
    <h2 class="wordmark">MORIVAL</h2>
    <p class="varietal">CABERNET FRANK</p>
    <p class="vintage">2015</p>
    <div class="footer">
      <span class="fine"></span>
      <span class="origin">Product of France</span>
      <span class="fine right">12% ALC</span>
    </div>
  </article>

</main>
</body>
</html>
```